Homemaking training schools needs a Business Card design

Designer, Hello!

No special requirements, good-looking enough.
--------------------------------------------------------------------------

Name: Marcus Dole
Chairman
Tel: 0574-71948263
Mobile: 13857420916
Email: kelvora@mailnest.example
Web: www.prt2019.example
Add: No.258, LanpingJie, BeiyuanQu, Ningbo, Zhejiang

LOGO
Ningbo PRT Homemaking Training School

Target Market(s)

pregnant women, mothers, infants, the elderly and families, including cleaning, cooking, nursing training.

Industry/Entity Type

Business

Contact Information for Business Card

Name: Marcus Dole
Chairman
Tel: 0574-71948263
Mobile: 13857420916
Email: kelvora@mailnest.example
Web: www.prt2019.example

LOGO

Font styles to use
Serif
Sans Serif
Decorative

Requirements
Nice to have
• Feels: clean, specifications, safety, comfort, warmth and happiness.

```html
<!DOCTYPE html>
<html lang="en">
<head>
<meta charset="utf-8">
<title>PingRuiTang Business Card</title>
<link href="https://fonts.googleapis.com/css2?family=Roboto:wght@400;500;700&display=swap" rel="stylesheet">
<style>
  :root {
    --bg: #ecebe8;
    --magenta: #ec1a8c;
    --blue: #1f7fc6;
    --blue-dark: #1669ad;
    --white: #ffffff;
    --ink: #1f7fc6;
  }
  * { margin: 0; padding: 0; box-sizing: border-box; }
  html, body { width: 1200px; height: 950px; overflow: hidden; }
  body {
    background: var(--bg);
    font-family: "Roboto", Arial, sans-serif;
    position: relative;
  }
  .card {
    position: absolute;
    width: 600px;
    height: 343px;
    box-shadow: 0 6px 18px rgba(0,0,0,0.18);
    overflow: hidden;
  }
  /* Back side */
  .card-back {
    left: 90px; top: 90px;
    background: var(--magenta);
  }
  .back-mark {
    position: absolute;
    left: 0; right: 0; top: 110px;
    text-align: center;
    color: var(--white);
    font-size: 40px;
    font-weight: 500;
    letter-spacing: 1px;
  }
  .back-mark .dot {
    display: block;
    width: 30px; height: 30px;
    margin: 0 auto 14px;
    border-radius: 50%;
    background: var(--white);
  }
  .back-web {
    position: absolute;
    left: 0; right: 0; bottom: 40px;
    text-align: center;
    color: var(--white);
    font-size: 15px;
    letter-spacing: 5px;
  }
  /* Front side */
  .card-front {
    left: 510px; top: 500px;
    background: var(--white);
  }
  .front-shape { position: absolute; inset: 0; }
  .brand {
    position: absolute;
    left: 355px; top: 135px;
    display: flex; align-items: center; gap: 10px;
    color: var(--ink);
    font-size: 34px;
    font-weight: 500;
  }
  .brand .dot {
    width: 14px; height: 14px; border-radius: 50%;
    background: var(--magenta);
  }
  .person {
    position: absolute;
    left: 40px; top: 48px;
    color: var(--white);
  }
  .person .name {
    color: var(--magenta);
    font-size: 20px;
    font-weight: 700;
  }
  .person .role { font-size: 15px; margin-top: 4px; }
  .address {
    position: absolute;
    left: 40px; top: 140px;
    color: var(--white);
    font-size: 14px;
    line-height: 1.4;
  }
  .contacts {
    position: absolute;
    left: 40px; top: 222px;
    list-style: none;
    color: var(--white);
    font-size: 14px;
    line-height: 1.55;
  }
  .contacts li { display: flex; align-items: center; gap: 10px; }
  .contacts svg { width: 12px; height: 12px; fill: var(--magenta); flex: none; }
</style>
</head>
<body>
  <section class="card card-back">
    <div class="back-mark"><span class="dot"></span>PingRuiTang</div>
    <div class="back-web">www.prt2019.example</div>
  </section>

  <section class="card card-front">
    <svg class="front-shape" viewBox="0 0 600 343" preserveAspectRatio="none">
      <path d="M0 0 H215 C250 120 330 260 470 343 H0 Z" fill="var(--blue)"/>
      <path d="M238 0 C275 125 360 255 520 320" fill="none" stroke="var(--blue)" stroke-width="5"/>
    </svg>

    <div class="brand"><span class="dot"></span>PingRuiTang</div>

    <div class="person">
      <div class="name">Marcus Dole</div>
      <div class="role">Chairman</div>
    </div>

    <div class="address">
      No.258, LanpingJie,<br>
      BeiyuanQu, Ningbo<br>
      Zhejiang
    </div>

    <ul class="contacts">
      <li><svg viewBox="0 0 12 12"><path d="M2 1h3l1 3-2 1a7 7 0 0 0 3 3l1-2 3 1v3c-6 0-9-3-9-9z"/></svg>0574-71948263</li>
      <li><svg viewBox="0 0 12 12"><rect x="3" y="0" width="6" height="12" rx="1"/></svg>13857420916</li>
      <li><svg viewBox="0 0 12 12"><path d="M0 2h12v8H0z"/></svg>kelvora@mailnest.example</li>
      <li><svg viewBox="0 0 12 12"><circle cx="6" cy="6" r="6"/></svg>www.prt2019.example</li>
    </ul>
  </section>
</body>
</html>
```